business card deign

Logo needs the following on it.
1. attached logo
2. Tagline - "If it chills the cooler or keeps the fun rolling...we bring it!"
3. Name- Dalton Pikes, Founder and CPO
4. Address - 412 E. Carver Avenue, Ste 2207, Tampa, FL. 33917
5. Phone - 555.318.4726

```html
<!DOCTYPE html>
<html lang="en">
<head>
<meta charset="utf-8">
<title>Koolby Business Card</title>
<link href="https://fonts.googleapis.com/css2?family=Montserrat:wght@400;500;700&display=swap" rel="stylesheet">
<style>
  :root {
    --backdrop: #979797;
    --card-light: #ffffff;
    --card-dark: #2a2a2a;
    --ink: #2b2b2b;
    --ink-soft: #3a3a3a;
    --paper: #ffffff;
  }
  * { margin: 0; padding: 0; box-sizing: border-box; }
  html, body {
    width: 1200px; height: 1059px; overflow: hidden;
    background: var(--backdrop);
    font-family: "Montserrat", sans-serif;
  }
  .canvas { position: relative; width: 1200px; height: 1059px; }
  .card {
    position: absolute;
    border-radius: 18px;
    overflow: hidden;
  }
  .card--front { left: 256px; top: 89px; width: 687px; height: 391px; background: var(--card-light); color: var(--ink); }
  .card--back  { left: 253px; top: 569px; width: 693px; height: 394px; background: var(--card-dark); color: var(--paper); }

  .brand-mark {
    position: absolute; left: 50%; transform: translateX(-50%);
    border-radius: 50%;
  }
  .card--front .brand-mark { top: 52px; width: 96px; height: 96px; background: var(--ink); }
  .card--back .brand-mark { top: 86px; width: 118px; height: 118px; background: var(--paper); }

  .brand-name {
    position: absolute; left: 0; right: 0; text-align: center;
    font-weight: 700; letter-spacing: 0.42em; text-indent: 0.42em;
    line-height: 1;
  }
  .card--front .brand-name { top: 170px; font-size: 30px; color: var(--ink); }
  .card--back .brand-name { top: 242px; font-size: 42px; color: var(--paper); }

  .person {
    position: absolute; right: 368px; top: 270px; text-align: right;
  }
  .person__name { font-size: 24px; font-weight: 700; letter-spacing: 0.02em; line-height: 1.1; }
  .person__role { font-size: 15.5px; font-weight: 400; margin-top: 3px; color: var(--ink-soft); }

  .divider {
    position: absolute; left: 343px; top: 248px; width: 1.5px; height: 90px;
    background: var(--ink);
  }

  .contact {
    position: absolute; left: 367px; top: 245px;
    font-size: 15.5px; font-weight: 400; color: var(--ink-soft); line-height: 1.45;
  }
  .contact__address { margin-bottom: 7px; }
  .contact__row { display: flex; align-items: center; gap: 7px; margin-bottom: 3px; }
  .contact__icon { width: 12px; height: 12px; flex: none; }

  .tagline {
    position: absolute; left: 0; right: 0; top: 342px; text-align: center;
    font-size: 16px; font-weight: 400; letter-spacing: 0.01em;
  }
</style>
</head>
<body>
<div class="canvas">

  <section class="card card--front">
    <div class="brand-mark" role="img" aria-label="Brand symbol area"></div>
    <div class="brand-name">KOOLBY</div>

    <div class="person">
      <div class="person__name">DALTON PIKES</div>
      <div class="person__role">Founder and CPO</div>
    </div>

    <div class="divider"></div>

    <div class="contact">
      <div class="contact__address">412 E. Carver Avenue<br>Ste 2207, Tampa, FL. 33917</div>
      <div class="contact__row">
        <svg class="contact__icon" viewBox="0 0 12 12" aria-hidden="true">
          <path d="M1 4.5 C1 2.5 3.5 1.8 6 1.8 S11 2.5 11 4.5 L8.6 5 L8.2 3.8 H3.8 L3.4 5 Z" fill="#2b2b2b"/>
          <rect x="2.5" y="5.5" width="7" height="5" rx="1" fill="#2b2b2b"/>
        </svg>
        <span>555.318.4726</span>
      </div>
      <div class="contact__row">
        <svg class="contact__icon" viewBox="0 0 12 12" aria-hidden="true">
          <path d="M1 5 L6 1.5 L11 5 V11 H1 Z" fill="none" stroke="#2b2b2b" stroke-width="1.3"/>
          <path d="M1 5 L6 8.5 L11 5" fill="none" stroke="#2b2b2b" stroke-width="1.3"/>
        </svg>
        <span>daltonpikes@koolbymail.com</span>
      </div>
    </div>
  </section>

  <section class="card card--back">
    <div class="brand-mark" role="img" aria-label="Brand symbol area"></div>
    <div class="brand-name">KOOLBY</div>
    <p class="tagline">If it chills the cooler or keeps the fun rolling...we bring it!</p>
  </section>

</div>
</body>
</html>
```